House-share and Room Rental Website (With Focus on the Bedroom Landing Page)

Looking for website design for our House-share (executive accommodation) and room rental business.

Our company name is: Lodgivo could also be written as LodGivo or lodgivo. Either is fine .. just looking for a nice clean catchy logo to go with the design.

EXAMPLES
These are examples of other websites in this field that are doing well. this is a kind of baseline.
https://nestpartners-example.com.au/
https://www.bunkora-example.com/
https://www.dwelzy-example.com/
https://www.habiquo-example.net/
https://www.cohabiscout-example.com.au/

Our business model is to rent rooms to people looking for high-quality accommodation. We fill the gap between those looking to rent rooms and those with rooms to rent. However, our model is slightly different from those already on the market as we looking to fill a massive gap in the market delivering upmarket rooms for rent.(Executive Accommodation) also in the back end will be coupled with a self management process in the back end.

We offer executive style accommodation that stands out above the rest. With special extras like fire safety.. and management processes that create happier homes. We are looking for a web design package that can help us grow and scale our business. We need a design that is captivating

Our MAIN focus is having a room landing page that stands out from the rest... The core of our business will rely on the promotion of the rooms in a share house... so the whole design relies on the BEDROOM landing page to drive results.

Target Market(s)

We have 2 markets we are aiming at ... the first market is people offering rooms to rent who want the highest rental return. The second market is people looking to rent safe, high-quality rooms, in houses that are well managed and looked after.

Industry/Entity Type

Share Economy

Logo Text

LodGivo

Number of Pages Required

5+ page

Font styles to use
Sans Serif

Colors
3276b5

Requirements
Must have
• A messaging system whereby we can create direct communication between those offering rooms and those looking for rooms.
• A call to action that says " Schedule an Inspection"
• Landing page for promoting rooms
• A home page for showing stock.
• Profile page for those selling rooms
• Profile page for those looking for rooms.
• A scheduling calendar for booking inspections
Nice to have
• Pages where new residents can lock in a room.. pay bond and rents.. and sign contracts
• Notifications
• SMS capabilities in the backend.
Should not have
• No script or handwriting fonts.

```html
<!DOCTYPE html>
<html lang="en">
<head>
<meta charset="utf-8">
<title>Lodgivo</title>
<link rel="stylesheet" href="https://fonts.googleapis.com/css2?family=Raleway:wght@400;500;700&family=Open+Sans:wght@400;600&display=swap">
<style>
:root{
  --brand:#3276b5;
  --brand-dark:#2a62a5;
  --hero-top:#4a78b6;
  --hero-bottom:#2f5f9e;
  --ink:#333a44;
  --muted:#8b8f96;
  --line:#c9cdd2;
  --band:#eef3fa;
  --tile:#eef3fa;
  --footer:#292929;
  --footer-text:#a9a9a9;
  --white:#ffffff;
}
*{box-sizing:border-box;margin:0;padding:0}
html,body{width:1200px;height:2711px;overflow:hidden;background:var(--white)}
body{position:relative;font-family:"Raleway",sans-serif;color:var(--ink)}

/* hero */
.hero{position:absolute;left:0;top:0;width:1200px;height:614px;
  background:radial-gradient(ellipse at 30% 35%,#7ea3d3 0%,rgba(126,163,211,0) 55%),
  linear-gradient(180deg,var(--hero-top),var(--hero-bottom));}
.brand{position:absolute;left:143px;top:20px;font-weight:500;font-size:36px;color:var(--white)}
.nav-item{position:absolute;top:32px;font-size:13.5px;color:var(--white);font-weight:500;white-space:nowrap}
.cta-outline{position:absolute;left:879px;top:18px;width:176px;height:46px;border:1.5px solid rgba(255,255,255,.85);border-radius:3px;color:var(--white);font-size:13.5px;display:flex;align-items:center;justify-content:center;font-weight:500}
.hero-title{position:absolute;left:0;width:1200px;top:263px;text-align:center;color:var(--white);font-size:31px;font-weight:400}
.hero-btn{position:absolute;left:545px;top:311px;width:111px;height:44px;border:1.5px solid rgba(255,255,255,.85);border-radius:2px;color:var(--white);font-size:14px;display:flex;align-items:center;justify-content:center}
.arrow{position:absolute;top:325px}

.section-title{position:absolute;left:0;width:1200px;text-align:center;color:var(--brand);font-size:33px;font-weight:400}

/* rooms */
.rooms{position:absolute;left:145px;top:750px;width:910px;display:grid;grid-template-columns:repeat(3,296px);gap:14px 11px}
.room-card{height:253px;border:1.5px solid var(--line);padding:7px}
.room-photo{height:175px;width:100%}
.room-card p{margin-top:11px;font-size:16px;line-height:20px;color:var(--ink);padding-right:6px}
.p1{background:linear-gradient(135deg,#6b3a22,#c9b9a8 55%,#e9e6e2)}
.p2{background:linear-gradient(160deg,#d7d3cc,#a9a496 50%,#2f7f8f)}
.p3{background:linear-gradient(140deg,#3d2c23,#a79887 50%,#5b3a28)}
.p4{background:linear-gradient(135deg,#1d1d1d,#9c9890 50%,#e6e2dd)}
.p5{background:linear-gradient(150deg,#7b6e62,#d8d1c8 50%,#4a3428)}
.p6{background:linear-gradient(135deg,#4f4a44,#c7c0b5 45%,#6d4a34)}
.btn{position:absolute;left:544px;width:112px;height:46px;background:var(--brand-dark);color:var(--white);font-size:15px;display:flex;align-items:center;justify-content:center;border-radius:2px}

/* testimonials */
.testimonials{position:absolute;left:0;top:1424px;width:1200px;height:569px;background:var(--band)}
.quote-side{position:absolute;top:166px;width:327px;height:183px;background:#fbfcfe;border-radius:4px;box-shadow:0 2px 6px rgba(0,0,0,.08);padding:22px 22px;text-align:center;font-family:"Open Sans",sans-serif;font-size:9.3px;line-height:16px;color:#a6aab0}
.quote-side .stars{margin-bottom:8px}
.quote-main{position:absolute;left:396px;top:137px;width:408px;height:228px;background:var(--brand-dark);border-radius:5px;padding:26px 20px;text-align:center;color:var(--white);font-family:"Open Sans",sans-serif;font-size:12.2px;line-height:22.6px}
.quote-main .stars{margin-bottom:4px}
.notch{position:absolute;left:50%;transform:translateX(-50%);bottom:-18px;width:0;height:0;border-left:16px solid transparent;border-right:16px solid transparent;border-top:18px solid var(--brand-dark)}
.notch.light{border-top-color:#fbfcfe;bottom:-12px;border-left-width:11px;border-right-width:11px;border-top-width:12px}
.person{position:absolute;text-align:center;font-family:"Open Sans",sans-serif;color:var(--muted);font-size:15px}
.person.main{color:#555;font-size:19px}
.dots{position:absolute;left:539px;top:471px;display:flex;gap:16px}
.dots i{width:16px;height:16px;border-radius:50%;background:#b3b6ba;display:block}
.dots i.on{background:var(--brand-dark)}

/* why us */
.features{position:absolute;left:145px;top:2127px;display:grid;grid-template-columns:repeat(4,216px);gap:0 15px}
.feature{height:143px;background:var(--tile);text-align:center;padding-top:24px}
.feature svg{display:block;margin:0 auto}
.feature p{margin-top:12px;font-size:15px;line-height:20px;color:#444}

/* footer */
.footer{position:absolute;left:0;top:2414px;width:1200px;height:297px;background:var(--footer)}
.footer h4{position:absolute;top:53px;font-weight:500;font-size:19px;color:#e4e4e4}
.links{position:absolute;top:90px;font-family:"Open Sans",sans-serif;font-size:11.5px;line-height:27px;color:var(--footer-text)}
.newsletter{position:absolute;left:670px;top:94px;width:217px;height:42px;background:#d9d9d9;display:flex;align-items:center;padding-left:16px;font-family:"Open Sans",sans-serif;font-size:11.5px;color:#444}
.newsletter svg{position:absolute;right:12px;top:13px}
.social{position:absolute;left:936px;top:92px;display:flex;gap:24px}
.social i{display:block;width:18px;height:18px;border-radius:50%;background:#9a9a9a}
.divider{position:absolute;left:145px;top:221px;width:910px;height:1px;background:#444}
.copyright{position:absolute;left:0;width:1200px;top:252px;text-align:center;font-family:"Open Sans",sans-serif;font-size:11.5px;color:#d0d0d0}
</style>
</head>
<body>

<header class="hero" role="img" aria-label="Softly lit bedroom with lamp and pillows, tinted blue">
  <div class="brand">Lodgivo</div>
  <span class="nav-item" style="left:530px">Home</span>
  <span class="nav-item" style="left:598px">Profile</span>
  <span class="nav-item" style="left:668px">Bond &amp; Rents</span>
  <span class="nav-item" style="left:780px">Contact Us</span>
  <div class="cta-outline">Schedule an Inspection</div>
  <h1 class="hero-title">Curabitur venenatis lacinia ornare</h1>
  <div class="hero-btn">Book Now</div>
  <svg class="arrow" style="left:58px" width="16" height="26" viewBox="0 0 16 26"><path d="M13 3 3 13l10 10" fill="none" stroke="#fff" stroke-width="4"/></svg>
  <svg class="arrow" style="left:1124px" width="16" height="26" viewBox="0 0 16 26"><path d="M3 3l10 10L3 23" fill="none" stroke="#fff" stroke-width="4"/></svg>
</header>

<h2 class="section-title" style="top:685px">Rooms Listing</h2>
<section class="rooms">
  <article class="room-card"><div class="room-photo p1" role="img" aria-label="Bedroom with large bed and window"></div><p>Vestibulum condimentum, risus ut posuere cursus velit.</p></article>
  <article class="room-card"><div class="room-photo p2" role="img" aria-label="Living room with teal sofa and shelves"></div><p>Pellentesque a imperdiet dolor et auctor est</p></article>
  <article class="room-card"><div class="room-photo p3" role="img" aria-label="Entrance hall with curved staircase"></div><p>Maecenas vel tortor accumsan quam varius imperdiet vel eget</p></article>
  <article class="room-card"><div class="room-photo p4" role="img" aria-label="Open living area with sofa and stairs"></div><p>Aenean facilisis tincidunt lectus id dictum nisi luctus eget</p></article>
  <article class="room-card"><div class="room-photo p5" role="img" aria-label="Hallway with staircase and wood floor"></div><p>Vivamus efficitur ex condimentum malesuada eros eget.</p></article>
  <article class="room-card"><div class="room-photo p6" role="img" aria-label="Bedroom with double bed and garden view"></div><p>Etiam massa elementum bibendum tellus venenatis, feugiat massa</p></article>
</section>
<div class="btn" style="top:1298px">View All</div>

<section class="testimonials">
  <h2 class="section-title" style="top:72px">Testimonials</h2>
  <div class="quote-side" style="left:42px">
    <div class="stars"><svg width="90" height="16" viewBox="0 0 90 16"><g fill="#a9adb3"><path id="s" d="M8 0l2.4 5 5.4.6-4 3.7 1.1 5.4L8 12 3.1 14.7l1.1-5.4-4-3.7L5.6 5z"/><use href="#s" x="18.5"/><use href="#s" x="37"/><use href="#s" x="55.5"/><use href="#s" x="74"/></g></svg></div>
    Suspendisse porttitor auctor vehicula. In sodales sem a lectus viverra, vitae varius nisi sodales. Aliquam cursus dolor vel interdum pellentesque. Fusce convallis venenatis pulvinar. Curabitur vel dapibus tellus. Vivamus dolor sapien, sollicitudin nec pulvinar sit amet, vulputate et elit. Phasellus accumsan sem sem, eu mattis ex vulputate quis.
    <span class="notch light"></span>
  </div>
  <div class="quote-main">
    <div class="stars"><svg width="112" height="20" viewBox="0 0 90 16"><g fill="#fff"><use href="#s"/><use href="#s" x="18.5"/><use href="#s" x="37"/><use href="#s" x="55.5"/><use href="#s" x="74"/></g></svg></div>
    Vestibulum condimentum, risus ut posuere cursus, velit justo accumsan sem, lobortis aliquet metus dui eu libero. Pellentesque a imperdiet dolor, et auctor est. Fusce sollicitudin lorem et luctus volutpat. Proin placerat dapibus gravida. In tristique tristique nulla eget hendrerit. Maecenas vel tortor accumsan quam varius imperdiet vel eget elit. Aenean facilisis.
    <span class="notch"></span>
  </div>
  <div class="quote-side" style="left:831px">
    <div class="stars"><svg width="90" height="16" viewBox="0 0 90 16"><g fill="#a9adb3"><use href="#s"/><use href="#s" x="18.5"/><use href="#s" x="37"/><use href="#s" x="55.5"/><use href="#s" x="74"/></g></svg></div>
    Sed iaculis nisl est, vitae sagittis risus fermentum sed. Donec lobortis, dui sed eleifend pellentesque, erat dui tincidunt urna, eu eleifend ante felis quis enim. Nam et turpis non turpis cursus rhoncus a et urna. Nunc tristique nec tortor vitae imperdiet. Sed elementum odio nunc, gravida mattis lorem interdum tempor. Etiam consequat lacus a felis viverra.
    <span class="notch light"></span>
  </div>
  <div class="person" style="left:42px;width:327px;top:385px">Maren</div>
  <div class="person main" style="left:396px;width:408px;top:410px">Tobias Wren</div>
  <div class="person" style="left:831px;width:327px;top:385px">Kellan</div>
  <div class="dots"><i class="on"></i><i></i><i></i><i></i></div>
</section>

<h2 class="section-title" style="top:2062px">Why Us?</h2>
<section class="features">
  <div class="feature">
    <svg width="36" height="40" viewBox="0 0 36 40"><path d="M18 2c2 7 10 11 10 21a10 10 0 0 1-20 0c0-5 3-8 5-11 0 4 2 6 4 6-2-5 0-11 1-16z" fill="var(--brand-dark)"/><rect x="4" y="36" width="28" height="3" fill="var(--brand-dark)"/></svg>
    <p>Fire Safety and<br>Management</p>
  </div>
  <div class="feature">
    <svg width="46" height="40" viewBox="0 0 46 40"><g fill="var(--brand-dark)"><rect x="2" y="8" width="5" height="28"/><rect x="2" y="24" width="42" height="7"/><rect x="39" y="24" width="5" height="12"/><circle cx="14" cy="18" r="5"/><path d="M21 14h17a6 6 0 0 1 6 6v4H21z"/></g></svg>
    <p>Furnished/unfurnished</p>
  </div>
  <div class="feature">
    <svg width="40" height="40" viewBox="0 0 40 40"><g fill="var(--brand-dark)"><ellipse cx="26" cy="13" rx="11" ry="10" transform="rotate(45 26 13)"/><path d="M17 20l4 4L7 38a3 3 0 0 1-4-4z"/></g></svg>
    <p>Kitchenette</p>
  </div>
  <div class="feature">
    <svg width="46" height="40" viewBox="0 0 46 40"><g fill="var(--brand-dark)"><path d="M2 2h42v28H2zm4 4v20h34V6z"/><rect x="19" y="30" width="8" height="5"/><rect x="12" y="35" width="22" height="3"/></g></svg>
    <p>TV</p>
  </div>
</section>
<div class="btn" style="top:2296px">View All</div>

<footer class="footer">
  <h4 style="left:145px">Links</h4>
  <div class="links" style="left:145px">Home<br>Profile<br>Bond &amp; Rents<br>Contact Us</div>
  <div class="links" style="left:242px">Schedule an Inspection<br>Register<br>Login</div>
  <h4 style="left:412px">Aliquam</h4>
  <div class="links" style="left:412px">Donec vestibulum<br>Quisque aliquet<br>Pellentesque<br>Etiam id</div>
  <div class="links" style="left:531px">Fusce vitae<br>Aenean placerat<br>Vestibulum ante<br>Vestibulum eget</div>
  <h4 style="left:670px">Newsletter Signup</h4>
  <div class="newsletter">Email Address
    <svg width="20" height="16" viewBox="0 0 20 16"><path d="M0 0h20v16H0z" fill="#333"/><path d="M1 1l9 7 9-7" fill="none" stroke="#d9d9d9" stroke-width="1.6"/></svg>
  </div>
  <h4 style="left:936px">Follow us on</h4>
  <div class="social"><i></i><i></i><i></i></div>
  <div class="divider"></div>
  <div class="copyright">Copyright &copy; 2019 Lodgivo. &nbsp;All rights reserved.</div>
</footer>

</body>
</html>
```